International Clinical Software Company needs a new business card design

We are looking for a new business card design for our company that has recently expanded into the UK market, making us a multinational company.
After having rebranded our website and produced a new style guide, we are looking for a business card that is creative and attention grabbing, while being consistent with the style and colour scheme used on the new website, www.plumvora.example
We produce care management technology for the aged care market, but the main aspect we aim to communicate is the human element of our software, and the way it assists in providing better care for aged people, and stronger relationships between aged people and the staff that care for them.
Our current business card is a dark green with gold text, which makes the text quite difficult to read, not very aesthetically appealing and the colour scheme looks quite dated.
We would like something fresh and modern, that can still be colourful but doesn't use large blocks of dark colour, and uses the colours within our logo.
Something tying in with the leaves that are used in our logo could work quite nicely, along with the Autumn/Fall colours of soft greens, yellows and reds (also in our existing logo). However also happy to look at fresh, completely out of the box ideas we may not have yet considered.
Target Market(s)
The people that receive this business card work in the aged card or health industry and are either corporate/management level staff or clinical (Registered Nurses, care workers etc.)
Industry/Entity Type
Health Product
Contact Information for Business Card
Company Name - BrindlewayCare
Company locations: United Kingdom, Australia, New Zealand
Staff Details:
Staff name: Derek Mallow
Staff job title: Executive Chairman
Staff email: d.mallow@plumvora.example
Office phone number: 01742 918576
Font styles to use
Other font styles liked:
- Calibri
Requirements
Must have
- Must include the BrindlewayCare brand name in it's current font
- Must include logo (3 leaves in gold circle)
- Must include Business Card Details
Nice to have
- Elements of gold
- White space
- Something autumn themed but not too cliched
Should not have
- No blue - used by a major competitor and we would like to differentiate from them
- Large blocks of dark green colour (the green that appears in our leaves on the logo on our current business card is the background colour and it is far too dark)

```html
<!DOCTYPE html>
<html lang="en">
<head>
<meta charset="utf-8">
<title>BrindlewayCare — Business Card</title>
<link href="https://fonts.googleapis.com/css2?family=Open+Sans:wght@300;400;600;700&display=swap" rel="stylesheet">
<style>
  :root {
    --page: #ecebe6;
    --card: #ffffff;
    --card-warm: #fbfaf6;
    --khaki: #a89d72;
    --wordmark: #8c8466;
    --ink-light: #ffffff;
    --leaf-yellow: #e8cf3a;
    --leaf-orange: #e08a22;
    --leaf-red: #b8402a;
    --leaf-green: #8aa33a;
    --leaf-brown: #6b3418;
  }
  * { box-sizing: border-box; margin: 0; padding: 0; }
  html, body {
    width: 1200px; height: 900px; overflow: hidden;
    background: var(--page);
    font-family: "Open Sans", Calibri, Arial, sans-serif;
  }
  .canvas {
    width: 1200px; height: 900px;
    display: flex; align-items: center; justify-content: center; gap: 30px;
  }
  .card {
    position: relative;
    width: 560px; height: 320px;
    background: var(--card);
    box-shadow: 0 6px 18px rgba(0,0,0,0.12);
    overflow: hidden;
  }
  /* Front */
  .card--front { background: linear-gradient(135deg, var(--card-warm), #f3f1ea); }
  .front-wordmark {
    position: absolute; left: 34px; top: 42px;
    font-size: 38px; font-weight: 300; letter-spacing: 1px;
    color: var(--wordmark);
  }
  .leaf-art { position: absolute; inset: 0; }
  /* Back */
  .card--back { display: flex; flex-direction: column; }
  .back-top {
    height: 186px;
    background: linear-gradient(180deg, #ffffff, #f2f2f0);
    display: flex; align-items: center; justify-content: center; gap: 18px;
  }
  .brand-dot {
    width: 82px; height: 82px; border-radius: 50%;
    border: 3px solid var(--khaki);
  }
  .brand-name {
    font-size: 34px; font-weight: 300; letter-spacing: 1px;
    color: var(--wordmark);
  }
  .back-band {
    flex: 1; background: var(--khaki); color: var(--ink-light);
    position: relative;
  }
  .person { position: absolute; left: 150px; top: 14px; text-align: right; }
  .person-name { font-size: 21px; font-weight: 700; line-height: 1.2; }
  .person-title { font-size: 15px; font-weight: 400; }
  .locations {
    position: absolute; left: 318px; top: 16px;
    font-size: 13px; line-height: 1.35;
  }
  .locations span { display: block; }
  .locations span + span { padding-left: 12px; }
  .contact {
    position: absolute; left: 0; right: 0; top: 88px;
    display: flex; justify-content: center; align-items: center; gap: 8px;
    font-size: 14px;
  }
  .contact svg { width: 13px; height: 13px; fill: var(--ink-light); }
</style>
</head>
<body>
<main class="canvas">
  <section class="card card--front">
    <svg class="leaf-art" viewBox="0 0 560 320" role="img" aria-label="Illustration of scattered autumn leaves in yellow, orange, red, green and brown sweeping across the card">
      <defs>
        <linearGradient id="leafTones" x1="0" y1="1" x2="1" y2="0">
          <stop offset="0" stop-color="var(--leaf-red)"/>
          <stop offset="0.3" stop-color="var(--leaf-orange)"/>
          <stop offset="0.6" stop-color="var(--leaf-yellow)"/>
          <stop offset="0.85" stop-color="var(--leaf-green)"/>
          <stop offset="1" stop-color="var(--leaf-yellow)"/>
        </linearGradient>
      </defs>
      <path d="M560 0 L560 150 C500 170 430 190 390 230 C350 260 300 300 250 320 L0 320 L0 300 C80 300 150 290 200 260 C250 220 280 170 300 120 C330 60 420 20 470 0 Z"
            fill="url(#leafTones)" opacity="0.85"/>
    </svg>
    <div class="front-wordmark">BrindlewayCare</div>
  </section>

  <section class="card card--back">
    <div class="back-top">
      <div class="brand-dot"></div>
      <div class="brand-name">BrindlewayCare</div>
    </div>
    <div class="back-band">
      <div class="person">
        <div class="person-name">Derek Mallow</div>
        <div class="person-title">Executive Chairman</div>
      </div>
      <div class="locations">
        <span>United Kingdom, Australia</span>
        <span>New Zealand</span>
      </div>
      <div class="contact">
        <svg viewBox="0 0 24 24" aria-hidden="true"><path d="M6.6 10.8a15.1 15.1 0 0 0 6.6 6.6l2.2-2.2a1 1 0 0 1 1-.25 11.4 11.4 0 0 0 3.6.57 1 1 0 0 1 1 1V20a1 1 0 0 1-1 1A17 17 0 0 1 3 4a1 1 0 0 1 1-1h3.5a1 1 0 0 1 1 1c0 1.25.2 2.45.57 3.6a1 1 0 0 1-.25 1Z"/></svg>
        <span>d.mallow@plumvora.example</span>
      </div>
    </div>
  </section>
</main>
</body>
</html>
```